Residential Remodeling Contractor needs updated business card

I need a new design for my business card.
Name of the company is Ridgefell Construction. I need a card that commands presence, strength, integrity. I have been in business for 28 years. I am a Residential Remodeling Contractor that covers all aspects of a residential remodel and build.

```html
<!DOCTYPE html>
<html lang="en">
<head>
<meta charset="utf-8">
<title>Ridgefell Construction – Business Card</title>
<link href="https://fonts.googleapis.com/css2?family=Open+Sans:wght@400;600;700&display=swap" rel="stylesheet">
<style>
  :root {
    --navy: #213f7e;
    --navy-deep: #1a3369;
    --paper: #ffffff;
    --stage: #222222;
    --ink-light: #ffffff;
  }
  * { box-sizing: border-box; margin: 0; padding: 0; }
  html, body {
    width: 1200px; height: 780px; overflow: hidden;
    background: var(--stage);
    font-family: "Open Sans", Arial, sans-serif;
  }
  .canvas {
    width: 1200px; height: 780px;
    display: flex; align-items: center; justify-content: center; gap: 40px;
  }
  .card {
    position: relative;
    width: 540px; height: 309px;
    border-radius: 3px;
    overflow: hidden;
  }

  /* Front */
  .card--front { background: var(--paper); color: var(--navy); }
  .front-band { position: absolute; inset: 0; }
  .brand-front {
    position: absolute; left: 262px; top: 44px;
    font-weight: 700; font-size: 27px; line-height: 1.1;
    letter-spacing: 0.5px; text-transform: uppercase;
    display: flex; align-items: center; gap: 12px;
  }
  .brand-mark {
    width: 16px; height: 16px; background: var(--navy); flex: none;
  }
  .person { position: absolute; left: 58px; top: 86px; }
  .person-name { font-weight: 700; font-size: 22px; line-height: 1.1; }
  .person-title { font-weight: 400; font-size: 12px; margin-top: 4px; margin-left: 40px; }
  .divider {
    position: absolute; left: 238px; top: 150px;
    width: 2px; height: 62px; background: var(--navy);
  }
  .contact-list {
    position: absolute; left: 256px; top: 150px;
    list-style: none; font-size: 13px; line-height: 20px;
  }
  .contact-list li { display: flex; align-items: center; gap: 8px; }
  .contact-list svg { width: 12px; height: 12px; fill: var(--navy); flex: none; }
  .address {
    position: absolute; left: 70px; bottom: 14px;
    color: var(--ink-light); font-size: 13px; letter-spacing: 0.2px;
  }

  /* Back */
  .card--back {
    background: var(--navy);
    display: flex; align-items: center; justify-content: center;
  }
  .brand-back {
    color: var(--ink-light);
    font-weight: 700; font-size: 38px; line-height: 1.1;
    letter-spacing: 1px; text-transform: uppercase;
    display: flex; align-items: center; gap: 18px;
  }
  .brand-back .brand-mark { background: var(--ink-light); width: 22px; height: 22px; }
</style>
</head>
<body>
<main class="canvas">

  <section class="card card--front">
    <svg class="front-band" viewBox="0 0 540 309" preserveAspectRatio="none" aria-hidden="true">
      <defs>
        <linearGradient id="accentFade" x1="0" y1="0" x2="1" y2="0">
          <stop offset="0" stop-color="#213f7e"/>
          <stop offset="0.6" stop-color="#213f7e" stop-opacity="0.25"/>
          <stop offset="1" stop-color="#213f7e"/>
        </linearGradient>
      </defs>
      <path d="M0 118 Q40 128 70 180 Q150 262 540 278 L540 309 L0 309 Z" fill="#213f7e"/>
      <path d="M22 128 Q60 150 90 195 Q170 252 470 262" fill="none" stroke="url(#accentFade)" stroke-width="2.5"/>
    </svg>

    <div class="brand-front">
      <span class="brand-mark"></span>
      <span>Ridgefell<br>Construction</span>
    </div>

    <div class="person">
      <p class="person-name">Marta Kolinska</p>
      <p class="person-title">Managing Director</p>
    </div>

    <div class="divider"></div>

    <ul class="contact-list">
      <li>
        <svg viewBox="0 0 24 24" aria-hidden="true"><path d="M6.6 10.8a15.1 15.1 0 0 0 6.6 6.6l2.2-2.2a1 1 0 0 1 1-.25 11.4 11.4 0 0 0 3.6.57 1 1 0 0 1 1 1V20a1 1 0 0 1-1 1A17 17 0 0 1 3 4a1 1 0 0 1 1-1h3.5a1 1 0 0 1 1 1c0 1.25.2 2.45.57 3.57a1 1 0 0 1-.25 1z"/></svg>
        <span>(555) 014-2286</span>
      </li>
      <li>
        <svg viewBox="0 0 24 24" aria-hidden="true"><path d="M2 5h20v14H2zm2 2v.4l8 5.1 8-5.1V7zm0 2.8V17h16V9.8l-8 5.1z"/></svg>
        <span>info@ridgefellbuild.com</span>
      </li>
      <li>
        <svg viewBox="0 0 24 24" aria-hidden="true"><path d="M12 2a10 10 0 1 0 0 20 10 10 0 0 0 0-20zm6.9 6h-3a15 15 0 0 0-1.3-3.9A8 8 0 0 1 18.9 8zM12 4a13 13 0 0 1 1.9 4h-3.8A13 13 0 0 1 12 4zM4.3 14a8 8 0 0 1 0-4h3.4a16 16 0 0 0 0 4zm.8 2h3a15 15 0 0 0 1.3 3.9A8 8 0 0 1 5.1 16zm3-8h-3a8 8 0 0 1 4.3-3.9A15 15 0 0 0 8.1 8zM12 20a13 13 0 0 1-1.9-4h3.8A13 13 0 0 1 12 20zm2.3-6H9.7a14 14 0 0 1 0-4h4.6a14 14 0 0 1 0 4zm.3 5.9a15 15 0 0 0 1.3-3.9h3a8 8 0 0 1-4.3 3.9zm1.7-5.9a16 16 0 0 0 0-4h3.4a8 8 0 0 1 0 4z"/></svg>
        <span>www.ridgefellbuild.com</span>
      </li>
    </ul>

    <p class="address">418 Quarry Bend Rd. Suite 120 Alder Falls, TX 75010</p>
  </section>

  <section class="card card--back">
    <div class="brand-back">
      <span class="brand-mark"></span>
      <span>Ridgefell<br>Construction</span>
    </div>
  </section>

</main>
</body>
</html>
```